Business Card for Fashion House

We need a business card design for our personalize fashion service for our customers. the business card should reflect reliability, luxury and creativity.
The brand Gravetto is extracted from "Graceful Velvetto"; Gravetto provides fashion designs sprinkled with luxury and style tailored for our elite clients character profile.
Gravetto is created for those who embody class and elegance with a passion for style.
Target Market(s)
Affluent Customers
Industry/Entity Type
Fashion
Contact Information for Business Card
Samira Haddadin
Fashion Designer
Telephone: +971 4 555 0192
Mobile +971 50 555 0147
Emal info@gravetto-example.com
Website www.gravetto-example.com
Social Media Youtube g+ Facebook Instagram Pin /gravetto
Font styles to use
Other font styles liked:
- Audrey provided
Look and feel
Each slider illustrates characteristics of the customer's brand and the style your logo design should communicate.

```html
<!DOCTYPE html>
<html lang="en">
<head>
<meta charset="utf-8">
<title>Gravetto — Business Card</title>
<link rel="stylesheet" href="https://fonts.googleapis.com/css2?family=Marcellus&family=Cormorant+Garamond:wght@500&display=swap">
<style>
  :root {
    --stage: #141414;
    --card-white: #fbfbfb;
    --ink: #1a1a1a;
    --band-black: #0d0d0d;
    --band-white: #ececec;
    --muted: #555555;
    --brand-font: "Marcellus", serif;
    --body-font: "Cormorant Garamond", serif;
  }
  * { margin: 0; padding: 0; box-sizing: border-box; }
  html, body { width: 1200px; height: 864px; overflow: hidden; }
  body {
    background: var(--stage);
    display: flex;
    align-items: center;
    justify-content: center;
    gap: 40px;
  }
  .card {
    position: relative;
    width: 520px;
    height: 300px;
    overflow: hidden;
    box-shadow: 0 12px 30px rgba(0,0,0,.6);
  }

  /* Front */
  .card-front { background: var(--card-white); color: var(--ink); }
  .brand-block {
    position: absolute;
    left: 70px;
    top: 44px;
    width: 200px;
    text-align: center;
  }
  .brand-dot {
    display: block;
    width: 34px;
    height: 34px;
    margin: 0 auto 14px;
    border: 2px solid var(--ink);
    border-radius: 50%;
  }
  .brand-name {
    font-family: var(--brand-font);
    font-size: 20px;
    letter-spacing: 0.42em;
    text-transform: uppercase;
    padding-left: 0.42em;
  }
  .contact-list {
    position: absolute;
    left: 64px;
    top: 136px;
    list-style: none;
    font-family: var(--body-font);
    font-size: 13px;
    line-height: 20px;
  }
  .contact-list li { display: flex; align-items: center; gap: 8px; }
  .contact-icon { width: 12px; height: 12px; flex: none; }
  .person {
    position: absolute;
    right: 40px;
    top: 116px;
    text-align: right;
  }
  .person-name {
    font-family: var(--brand-font);
    font-size: 14px;
    letter-spacing: 0.04em;
    text-transform: uppercase;
  }
  .person-role {
    font-family: var(--body-font);
    font-size: 12px;
    color: var(--muted);
  }
  .front-band {
    position: absolute;
    left: 0; right: 0;
    top: 226px;
    height: 30px;
    background: linear-gradient(180deg, #2a2a2a, var(--band-black));
  }
  .front-strip {
    position: absolute;
    left: 0; right: 0;
    top: 262px;
    height: 22px;
    background: var(--band-white);
  }

  /* Back */
  .card-back { background: linear-gradient(160deg, #1f1f1f, var(--band-black) 60%); }
  .back-ring {
    position: absolute;
    left: 200px;
    top: 50px;
    width: 120px;
    height: 120px;
    border: 3px solid rgba(255,255,255,.07);
    border-radius: 50%;
  }
  .back-band {
    position: absolute;
    left: 0; right: 0;
    top: 196px;
    height: 44px;
    background: linear-gradient(180deg, #f4f4f4, #cfcfcf);
    display: flex;
    align-items: center;
    justify-content: center;
  }
  .back-band .brand-name { color: var(--ink); font-size: 20px; }
  .back-strip {
    position: absolute;
    left: 0; right: 0;
    top: 252px;
    height: 16px;
    background: #bdbdbd;
  }
</style>
</head>
<body>

<section class="card card-front" aria-label="Business card front">
  <div class="brand-block">
    <span class="brand-dot" aria-hidden="true"></span>
    <div class="brand-name">Gravetto</div>
  </div>

  <ul class="contact-list">
    <li>
      <svg class="contact-icon" viewBox="0 0 12 12" aria-hidden="true"><circle cx="6" cy="6" r="5.4" fill="none" stroke="#1a1a1a" stroke-width="0.9"/><path d="M3.6 4.6h4.8v1.2H3.6zM4.4 5.8h3.2v2.2H4.4z" fill="#1a1a1a"/></svg>
      +971 4 555 0192
    </li>
    <li>
      <svg class="contact-icon" viewBox="0 0 12 12" aria-hidden="true"><circle cx="6" cy="6" r="5.4" fill="none" stroke="#1a1a1a" stroke-width="0.9"/><rect x="4.3" y="3" width="3.4" height="6" rx="0.6" fill="none" stroke="#1a1a1a" stroke-width="0.9"/></svg>
      +971 50 555 0147
    </li>
    <li>
      <svg class="contact-icon" viewBox="0 0 12 12" aria-hidden="true"><circle cx="6" cy="6" r="5.4" fill="none" stroke="#1a1a1a" stroke-width="0.9"/><rect x="3.3" y="4" width="5.4" height="4" fill="none" stroke="#1a1a1a" stroke-width="0.8"/><path d="M3.3 4L6 6.2 8.7 4" fill="none" stroke="#1a1a1a" stroke-width="0.8"/></svg>
      info@gravetto-example.com
    </li>
    <li>
      <svg class="contact-icon" viewBox="0 0 12 12" aria-hidden="true"><circle cx="6" cy="6" r="5.4" fill="none" stroke="#1a1a1a" stroke-width="0.9"/><ellipse cx="6" cy="6" rx="2" ry="5.4" fill="none" stroke="#1a1a1a" stroke-width="0.7"/><path d="M0.6 6h10.8" stroke="#1a1a1a" stroke-width="0.7"/></svg>
      www.gravetto-example.com
    </li>
  </ul>

  <div class="person">
    <div class="person-name">Samira Haddadin</div>
    <div class="person-role">Fashion Designer</div>
  </div>

  <div class="front-band"></div>
  <div class="front-strip"></div>
</section>

<section class="card card-back" aria-label="Business card back">
  <span class="back-ring" aria-hidden="true"></span>
  <div class="back-band">
    <div class="brand-name">Gravetto</div>
  </div>
  <div class="back-strip"></div>
</section>

</body>
</html>
```